Designer Instructions – Updated Referral Program Flyer

(Based on the mock-up in “Brief Layout and Instructions.pdf”)

OVERALL STYLE + LAYOUT

Maintain the same general layout, structure, and flow as the mock-up flyer (front and back).

This is an update of an older flyer, not a full redesign — keep the same sections, proportions, and overall visual feel, but with cleaner, more modern design improvements.

The final flyer should look clean, bold, professional, and high-impact, geared toward realtors, property managers, and contractors who refer work.

FRONT SIDE INSTRUCTIONS
1. Header Section

Remove the Rebuild Harbor Crest logo from the top banner.
(Shown on page 1 of the PDF)

2. Main Headline

Keep the same three-line structure:
EARN
UNLIMITED
CASH

Center it, maximize impact, and increase the font size of CASH so all three words match in importance.

Make the headline bold, clean, and the main focal point.

3. Cash Incentive Box

Keep the "$500 minimum OR 10% per referral" box, but upgrade the graphics to look sharper and more modern.

Ensure the wording matches exactly what’s in the mock-up.

4. Premier Partner Program Ribbon

Clean up and modernize the "PREMIER PARTNER PROGRAM" bar while keeping the same position and structure.

Ensure the checkmark badge remains crisp and professional.

5. Supporting Icons Section

Keep the four icons/benefit boxes (Guaranteed Payout, Free Evaluations, Affordable Solutions, Industry Leaders) in the same order.

Update the icons to cleaner, more modern styles — but maintain the same meanings.

Improve alignment and spacing for sharper visual consistency.

6. Remove Icons in Contact Area

At the bottom (“CALL TEXT OR BOOK ONLINE 858-471-6093 BrightlaneRenovate.com”), remove the phone and internet icons, as noted on page 2 of the PDF.

7. Replace All Images

I (Dorian) will provide all updated stock images separately via email.

Replace the flood/water-damage imagery and roof leak with the new images I send.

Keep image placement and proportions the same as the mock-up.

BACK SIDE INSTRUCTIONS
1. Header Image + “REFER / EARN” Section

Maintain the same large split-image layout (“The more you refer, the more you earn”).

Replace all background imagery with the new assets I will send.

Keep the CASH FLOW image section but modernize the type and spacing.

2. “HOW IT WORKS” Section

Preserve the three-column layout:

Refer Flood, Water & Mold Damage

We Take Care of Everything (evaluations/insurance)

Get Paid to Share

Update images, tighten spacing, and use modern iconography.

3. Remove Phone/Internet Icons

Same as the front side — remove small communication icons and keep only the text/number/URL.

4. Bottom Contact Bar

Keep the blue bar, same wording, same layout — just modernize the style if needed for clarity.

5. Replace All Back-Side Images

Again, I will email you the image assets.

Keep the layout EXACT — just update with higher-quality photos and improved design.

TEXT CONTENT (Keep as-is unless spacing adjustments needed)

All text shown in the PDF should remain exactly the same unless spacing or visual balance requires minor adjustments.
Example from page 3:

“REFER FLOOD, MOLD & CONSTRUCTION JOBS”

“We Schedule a Free Estimate. If Approved, You Get Paid.”

“Everybody Benefits From Referrals”

Everything stays, just refreshed and visually improved.

DESIGN GOALS

Flyer should look high-end and trustworthy, not salesy.

Consistent color theme: blues, whites, yellows, same palette as original.

Use bold, modern fonts with strong readability.

Ensure all headlines pop and all benefit boxes are clean, well-aligned, and evenly spaced.

The final result should feel like a premium referral program flyer for a top-tier restoration/remodel company.

FILES I WILL PROVIDE

I will send the designer:

All replacement stock photos

Any updated logos (if needed)

Original high-resolution version of the mock-up (if available)

Any additional icons preferred

Colors
0054AA
0677BA
7BADD7
CADEEF
E8F1F8

Requirements
Must have
• Designer Instructions – Updated Referral Program Flyer (Based on the mock-up in “Brief Layout and Instructions.pdf”) OVERALL STYLE + LAYOUT Maintain the same general layout, structure, and flow as the mock-up flyer (front and back). This is an update of an older flyer, not a full redesign — keep the same sections, proportions, and overall visual feel, but with cleaner, more modern design improvements. The final flyer should look clean, bold, professional, and high-impact, geared toward realtors, property managers, and contractors who refer work. FRONT SIDE INSTRUCTIONS 1. Header Section Remove the Rebuild Harbor Crest logo from the top banner. (Shown on page 1 of the PDF) 2. Main Headline Keep the same three-line structure: EARN UNLIMITED CASH Center it, maximize impact, and increase the font size of CASH so all three words match in importance. Make the headline bold, clean, and the main focal point. 3. Cash Incentive Box Keep the "$500 minimum OR 10% per referral" box, but upgrade the graphics to look sharper and more modern. Ensure the wording matches exactly what’s in the mock-up. 4. Premier Partner Program Ribbon Clean up and modernize the "PREMIER PARTNER PROGRAM" bar while keeping the same position and structure. Ensure the checkmark badge remains crisp and professional. 5. Supporting Icons Section Keep the four icons/benefit boxes (Guaranteed Payout, Free Evaluations, Affordable Solutions, Industry Leaders) in the same order. Update the icons to cleaner, more modern styles — but maintain the same meanings. Improve alignment and spacing for sharper visual consistency. 6. Remove Icons in Contact Area At the bottom (“CALL TEXT OR BOOK ONLINE 858-471-6093 BrightlaneRenovate.com”), remove the phone and internet icons, as noted on page 2 of the PDF. 7. Replace All Images I (Dorian) will provide all updated stock images separately via email. Replace the flood/water-damage imagery and roof leak with the new images I send. Keep image placement and proportions the same as the mock-up. BACK SIDE INSTRUCTIONS 1. Header Image + “REFER / EARN” Section Maintain the same large split-image layout (“The more you refer, the more you earn”). Replace all background imagery with the new assets I will send. Keep the CASH FLOW image section but modernize the type and spacing. 2. “HOW IT WORKS” Section Preserve the three-column layout: Refer Flood, Water & Mold Damage We Take Care of Everything (evaluations/insurance) Get Paid to Share Update images, tighten spacing, and use modern iconography. 3. Remove Phone/Internet Icons Same as the front side — remove small communication icons and keep only the text/number/URL. 4. Bottom Contact Bar Keep the blue bar, same wording, same layout — just modernize the style if needed for clarity. 5. Replace All Back-Side Images Again, I will email you the image assets. Keep the layout EXACT — just update with higher-quality photos and improved design. TEXT CONTENT (Keep as-is unless spacing adjustments needed) All text shown in the PDF should remain exactly the same unless spacing or visual balance requires minor adjustments. Example from page 3: “REFER FLOOD, MOLD & CONSTRUCTION JOBS” “We Schedule a Free Estimate. If Approved, You Get Paid.” “Everybody Benefits From Referrals” Everything stays, just refreshed and visually improved. DESIGN GOALS Flyer should look high-end and trustworthy, not salesy. Consistent color theme: blues, whites, yellows, same palette as original. Use bold, modern fonts with strong readability. Ensure all headlines pop and all benefit boxes are clean, well-aligned, and evenly spaced. The final result should feel like a premium referral program flyer for a top-tier restoration/remodel company. FILES I WILL PROVIDE I will send the designer: All replacement stock photos Any updated logos (if needed) Original high-resolution version of the mock-up (if available) Any additional icons preferred

```html
<!DOCTYPE html>
<html lang="en">
<head>
<meta charset="utf-8">
<title>Referral Partner Program Flyer</title>
<link href="https://fonts.googleapis.com/css2?family=Anton&family=Oswald:wght@400;500;600;700&family=Poppins:ital,wght@0,400;0,500;0,600;0,700;0,800;0,900;1,400;1,500&display=swap" rel="stylesheet">
<style>
  :root {
    --navy: #1b2452;
    --white: #ffffff;
    --yellow: #f7e62c;
    --gold: #fbc516;
    --orange: #f7931e;
    --ink: #1b2452;
    --photo-light: #d9e3ea;
    --photo-mid: #9fb8cc;
    --money-light: #e6e6df;
    --money-mid: #a9ada4;
  }
  * { box-sizing: border-box; margin: 0; padding: 0; }
  html, body { width: 1200px; height: 1200px; overflow: hidden; background: var(--white); }
  body { position: relative; font-family: "Poppins", sans-serif; color: var(--ink); }

  .flyer { position: absolute; left: 205px; width: 797px; height: 514px; overflow: hidden; background: var(--white); box-shadow: 0 6px 24px rgba(0,0,0,0.12); }
  .flyer--front { top: 67px; }
  .flyer--back { top: 625px; }
  .flyer__shapes { position: absolute; inset: 0; }

  .gradient-text {
    background: linear-gradient(90deg, var(--yellow) 0%, var(--gold) 45%, var(--orange) 100%);
    -webkit-background-clip: text; background-clip: text; color: transparent;
  }

  /* front headline */
  .headline { position: absolute; left: 36px; top: 30px; width: 345px; font-family: "Poppins", sans-serif; font-weight: 800; color: var(--white); }
  .headline__top { font-size: 36.5px; line-height: 1; letter-spacing: -0.3px; }
  .headline__cash { font-size: 120px; font-weight: 900; line-height: 0.9; letter-spacing: -7px; margin-top: 6px; margin-left: -4px; }
  .headline__sub { font-size: 22.5px; line-height: 1; letter-spacing: -0.2px; margin-top: 10px; }

  .badge { position: absolute; border-radius: 50%; background: var(--navy); border: 6px solid var(--white); box-shadow: 0 0 0 1px rgba(27,36,82,0.15); display: flex; flex-direction: column; align-items: center; justify-content: center; text-align: center; color: var(--white); }
  .badge--offer { left: 459px; top: 34px; width: 134px; height: 134px; }
  .badge--partner { left: 408px; top: 165px; width: 134px; height: 134px; }
  .offer__amount { font-family: "Oswald", sans-serif; font-weight: 600; font-size: 34px; line-height: 1; color: var(--yellow); }
  .offer__label { font-style: italic; font-size: 10.5px; line-height: 1.1; letter-spacing: 0.3px; }
  .offer__rule { width: 90px; height: 1.5px; background: var(--white); margin: 4px 0 6px; }
  .offer__note { font-style: italic; font-size: 6.5px; letter-spacing: 0.3px; margin-top: 2px; }
  .partner__top { font-weight: 700; font-size: 12.5px; color: var(--yellow); line-height: 1; }
  .partner__word { font-family: "Oswald", sans-serif; font-weight: 500; font-size: 16px; line-height: 1.1; margin: 4px 0; }
  .partner__tick { width: 34px; height: 34px; }

  .tagline { position: absolute; left: 36px; top: 255px; font-weight: 800; font-size: 25px; line-height: 1.3; color: var(--navy); }
  .tagline__accent { color: var(--orange); }

  .benefits { position: absolute; left: 34px; top: 328px; width: 430px; display: grid; grid-template-columns: 228px 200px; row-gap: 18px; }
  .benefit { display: flex; gap: 10px; align-items: flex-start; }
  .benefit__icon { flex: none; width: 40px; height: 40px; border-radius: 50%; border: 1.5px solid var(--gold); display: flex; align-items: center; justify-content: center; margin-top: 2px; }
  .benefit__icon svg { width: 24px; height: 24px; }
  .benefit__title { font-weight: 700; font-size: 12px; line-height: 1.2; color: var(--navy); }
  .benefit__text { font-size: 9.6px; line-height: 1.3; margin-top: 3px; color: var(--navy); }

  /* contact bar */
  .contact { position: absolute; left: 40px; top: 459px; color: var(--white); }
  .contact__label { font-size: 13.5px; line-height: 1; letter-spacing: 0.2px; }
  .contact__phone { font-weight: 700; font-size: 25px; line-height: 1; color: var(--yellow); margin-top: 6px; letter-spacing: 0.3px; }
  .contact__site { position: absolute; left: 291px; top: 478px; font-weight: 700; font-size: 15px; color: var(--white); }

  /* back headline */
  .earn-head { position: absolute; left: 48px; top: 26px; display: flex; gap: 10px; align-items: flex-start; font-family: "Anton", sans-serif; }
  .earn-head__stack { display: flex; flex-direction: column; width: 152px; color: var(--white); }
  .earn-head__line { font-size: 31px; line-height: 1; letter-spacing: -0.3px; white-space: nowrap; }
  .earn-head__refer { font-size: 72px; line-height: 0.92; letter-spacing: -1px; margin: 2px 0; }
  .earn-head__big { font-size: 140px; line-height: 0.86; letter-spacing: -1px; margin-top: 2px; }
  .how-title { position: absolute; left: 48px; top: 154px; font-family: "Oswald", sans-serif; font-weight: 500; font-size: 26px; line-height: 1; color: var(--white); }

  .steps { position: absolute; left: 36px; top: 201px; width: 420px; display: flex; flex-direction: column; gap: 9px; }
  .step { display: flex; gap: 10px; height: 74px; }
  .step__media { flex: none; width: 197px; height: 74px; border-radius: 8px; }
  .step__media--equipment { background: linear-gradient(120deg, #3a8fb5 0%, #8fb6c9 55%, #d9d6cc 100%); }
  .step__media--estimate { background: linear-gradient(120deg, #6aa1d3 0%, #b7a08a 55%, #4f7a3e 100%); }
  .step__media--share { background: linear-gradient(120deg, #4f9ad8 0%, #cfe3f4 50%, #f1d52a 100%); }
  .step__title { font-weight: 700; font-size: 13.5px; line-height: 1.3; color: var(--orange); }
  .step__text { font-size: 10px; line-height: 1.3; color: #111; margin-top: 3px; }
</style>
</head>
<body>

<section class="flyer flyer--front" aria-label="Front of referral flyer">
  <svg class="flyer__shapes" viewBox="0 0 797 514" aria-hidden="true">
    <defs>
      <linearGradient id="kitchenTone" x1="0" y1="0" x2="1" y2="1">
        <stop offset="0" stop-color="#e4eaef"/>
        <stop offset="0.55" stop-color="#b8cbd9"/>
        <stop offset="1" stop-color="#5c6570"/>
      </linearGradient>
    </defs>
    <rect width="797" height="239" fill="#1b2452"/>
    <path d="M558 0 Q420 270 596 514 L797 514 L797 0 Z" fill="#f7931e"/>
    <path d="M0 446 L478 446 Q502 446 518 463 L566 514 L0 514 Z" fill="#1b2452"/>
    <path d="M575 0 Q445 270 617 514 L797 514 L797 0 Z" fill="url(#kitchenTone)"/>
  </svg>
  <div role="img" aria-label="Photo of a modern kitchen with water pouring through a hole in the ceiling" style="position:absolute;left:560px;top:0;width:237px;height:514px;"></div>

  <h1 class="headline">
    <span class="headline__top" style="display:block">EARN UNLIMITED</span>
    <span class="headline__cash gradient-text" style="display:block">CASH</span>
    <span class="headline__sub" style="display:block">GET PAID TOREFER A FLOOD</span>
  </h1>

  <div class="badge badge--offer">
    <span class="offer__amount">$500</span>
    <span class="offer__label">MINIMUM</span>
    <span class="offer__rule"></span>
    <span class="offer__amount">10%</span>
    <span class="offer__note">PER REFERRAL</span>
  </div>

  <div class="badge badge--partner">
    <span class="partner__top">PREMIER</span>
    <span class="partner__word">PARTNER</span>
    <svg class="partner__tick" viewBox="0 0 34 34" aria-hidden="true">
      <circle cx="17" cy="17" r="15" fill="#f7e62c" stroke="#ffffff" stroke-width="2"/>
      <path d="M10 17.5 L15 22.5 L24.5 12" fill="none" stroke="#1b2452" stroke-width="3.2" stroke-linecap="round" stroke-linejoin="round"/>
    </svg>
    <span class="partner__word">PROGRAM</span>
  </div>

  <h2 class="tagline">PARTNER WITH US &amp;<br><span class="tagline__accent">EVERYBODY WINS!</span></h2>

  <div class="benefits">
    <div class="benefit">
      <span class="benefit__icon">
        <svg viewBox="0 0 24 24" fill="none" stroke="#1b2452" stroke-width="1.6" stroke-linejoin="round" stroke-linecap="round"><path d="M12 2.5l2.2 1.6 2.7-.2.9 2.6 2.3 1.4-.8 2.6.8 2.6-2.3 1.4-.9 2.6-2.7-.2L12 21.5l-2.2-1.6-2.7.2-.9-2.6-2.3-1.4.8-2.6-.8-2.6 2.3-1.4.9-2.6 2.7.2z"/><path d="M8.5 12l2.4 2.4 4.6-4.8"/></svg>
      </span>
      <div>
        <h3 class="benefit__title">GUARANTEEDPAYOUT</h3>
        <p class="benefit__text">Minimum $500 or 10% of Total<br>Invoice Paid Fast</p>
      </div>
    </div>
    <div class="benefit">
      <span class="benefit__icon">
        <svg viewBox="0 0 24 24" fill="none" stroke="#1b2452" stroke-width="1.6" stroke-linejoin="round" stroke-linecap="round"><rect x="4" y="3" width="11" height="16" rx="1.5"/><path d="M7 8h5M7 11h5M7 14h3"/><rect x="13" y="12" width="7" height="9" rx="1"/><path d="M15 15h3M15 18h3"/></svg>
      </span>
      <div>
        <h3 class="benefit__title">FREE ESTIMATES</h3>
        <p class="benefit__text">Fast &amp; Free Inspections<br>&amp; Written Estimates</p>
      </div>
    </div>
    <div class="benefit">
      <span class="benefit__icon">
        <svg viewBox="0 0 24 24" fill="none" stroke="#1b2452" stroke-width="1.6" stroke-linejoin="round" stroke-linecap="round"><circle cx="13" cy="9" r="4.5"/><path d="M13 6.8v4.4M11.8 10.3c.4.6 2.4.6 2.4-.4s-2.4-.6-2.4-1.6 2-1 2.4-.4"/><path d="M3 19l3-2.5h5l4 1.5 5-3"/><path d="M3 16h3"/></svg>
      </span>
      <div>
        <h3 class="benefit__title">AFFORDABLE SOLUTIONS</h3>
        <p class="benefit__text">Lowest Out of Pocket Costs for<br>Your Customers</p>
      </div>
    </div>
    <div class="benefit">
      <span class="benefit__icon">
        <svg viewBox="0 0 24 24" fill="none" stroke="#1b2452" stroke-width="1.6" stroke-linejoin="round" stroke-linecap="round"><path d="M12 2.5l1.2 2.4 2.6.4-1.9 1.8.5 2.6L12 8.5l-2.4 1.2.5-2.6-1.9-1.8 2.6-.4z"/><rect x="4" y="14" width="4.5" height="7"/><rect x="9.75" y="12" width="4.5" height="9"/><rect x="15.5" y="15.5" width="4.5" height="5.5"/></svg>
      </span>
      <div>
        <h3 class="benefit__title">INDUSTRY LEADERS</h3>
        <p class="benefit__text">Licensed &amp; Certified Experts<br>Provide 100% Guarantee</p>
      </div>
    </div>
  </div>

  <div class="contact">
    <p class="contact__label">CALL TEXT OR BOOK ONLINE</p>
    <p class="contact__phone">858-471-6093</p>
  </div>
  <p class="contact__site">BrightlaneRenovate.com</p>
</section>

<section class="flyer flyer--back" aria-label="Back of referral flyer">
  <svg class="flyer__shapes" viewBox="0 0 797 514" aria-hidden="true">
    <defs>
      <linearGradient id="moneyTone" x1="0" y1="0" x2="1" y2="1">
        <stop offset="0" stop-color="#ecece6"/>
        <stop offset="0.5" stop-color="#b9bdb4"/>
        <stop offset="1" stop-color="#e2e3dc"/>
      </linearGradient>
    </defs>
    <rect width="797" height="197" fill="#1b2452"/>
    <path d="M556 0 Q418 270 596 514 L797 514 L797 0 Z" fill="#f7931e"/>
    <path d="M0 446 L478 446 Q502 446 518 463 L566 514 L0 514 Z" fill="#1b2452"/>
    <path d="M574 0 Q438 270 616 514 L797 514 L797 0 Z" fill="url(#moneyTone)"/>
  </svg>
  <div role="img" aria-label="Photo of scattered hundred-dollar bills with letter tiles spelling cash flow" style="position:absolute;left:560px;top:0;width:237px;height:514px;"></div>

  <h1 class="earn-head">
    <span class="earn-head__stack">
      <span class="earn-head__line">THE MORE YOU</span>
      <span class="earn-head__refer gradient-text">REFER</span>
      <span class="earn-head__line">THE MORE YOU</span>
    </span>
    <span class="earn-head__big gradient-text">EARN</span>
  </h1>
  <h2 class="how-title">HOW IT WORKS</h2>

  <div class="steps">
    <div class="step">
      <div class="step__media step__media--equipment" role="img" aria-label="Photo of water-drying fans and dehumidifiers in a room"></div>
      <div>
        <h3 class="step__title">REFER FLOOD, MOLD &amp;<br>CONSTRUCTION JOBS:</h3>
        <p class="step__text">It’s Simple to Refer 24/7:<br>Call, Text or Book Online.</p>
      </div>
    </div>
    <div class="step">
      <div class="step__media step__media--estimate" role="img" aria-label="Photo of an estimate clipboard held in front of a house"></div>
      <div>
        <h3 class="step__title">WE TAKE CARE OF<br>EVERYTHING:</h3>
        <p class="step__text">We Schedule a Free Estimate.<br>If Approved, You Get Paid.</p>
      </div>
    </div>
    <div class="step">
      <div class="step__media step__media--share" role="img" aria-label="Photo of a yellow road sign reading get paid to share against a blue sky"></div>
      <div>
        <h3 class="step__title" style="text-transform:none">Everybody Benefits<br>From Referrals</h3>
        <p class="step__text">We Provide Expert Quality<br>Work for Affordable Price.</p>
      </div>
    </div>
  </div>

  <div class="contact">
    <p class="contact__label">CALL TEXT OR BOOK ONLINE</p>
    <p class="contact__phone">858-471-6093</p>
  </div>
  <p class="contact__site">BrightlaneRenovate.com</p>
</section>

</body>
</html>
```